A start-up named "Corvane Therapeutics" - needs a new PowerPoint design

We need a new PowerPoint Design for an early-stage start-up named "Corvane Therapeutics" seeking to disrupt the current approach towards drug discovery within aging disorders.

We would like to build on Corvane's legacy, the founder of the modern science of genetics, by employing a multidisciplinary approach, experimenting, and providing elderly patients the attention they deserve.

We have selected the suffix "therapeutics" intentionally as it stands for (a medicine) the treatment of disease; the science of healing. Alzheimer’s treatment is a huge, urgent, unmet need:
- Shift from a disease-management system to a preventive medicine system
- Focus on increasing the health span, not only the life span

Target Market(s)

Pharma/ Biotech Executives Medical Institutions Healthcare professionals (MDs, nurses, payors, pharmacists, etc.) Patients

Industry/Entity Type

Healthcare

Other font styles liked:
• Celias

Colors
0054AA
0677BA
7BADD7
CADEEF
E8F1F8
E54698
E96AAD
F1A4CE
F9D9EA
FCEFF6
A7469A
B969AE
D3A5CF
EDDBEB
F8F0F9
6B429C
8869AF
B7A5CE
E3DAEB
F3F0F8

Requirements
Must have
• - differentiate from other companies named after Corvane - differentiate from other Pharma/ Biotech companies
Nice to have
• simplicity/ minimalist logo vivid colors gradient 3D Life-Sciences inspired Simple geometry Balance
Should not have
• mascot/ emblem watermark logo animated ink style nature-inspired inventive typography artistic chaos

```html
<!DOCTYPE html>
<html lang="en">
<head>
<meta charset="utf-8">
<title>Corvane Therapeutics – Presentation Slides</title>
<link href="https://fonts.googleapis.com/css2?family=Montserrat:wght@400;500;600&display=swap" rel="stylesheet">
<style>
  :root{
    --board:#4a4b4e;
    --white:#ffffff;
    --ink:#1c1c2a;
    --blue:#2f6ff5;
    --blue-deep:#2a55d8;
    --violet:#7a12d6;
    --violet-mid:#5b2ee0;
    --cyan:#1aa6e6;
    --indigo:#3a2a8c;
    --plum:#7a1f6e;
    --navy:#1b2a6b;
    --heading-blue:#2f5fc8;
    --heading-violet:#4b3aa8;
  }
  *{margin:0;padding:0;box-sizing:border-box}
  html,body{width:1200px;height:3413px;overflow:hidden;background:var(--board)}
  body{font-family:"Montserrat",sans-serif;color:var(--ink);position:relative}
  .slide{position:absolute;left:49px;width:1102px;height:620px;overflow:hidden}
  .slide--cover{top:52px;background:linear-gradient(180deg,#3a7cf6 0%,#3a63ee 100%)}
  .slide--genetics{top:715px;background:var(--white)}
  .slide--columns{top:1377px;background:linear-gradient(160deg,#7a10d4 0%,#5a34ea 55%,#3d66f2 100%)}
  .slide--metrics{top:2041px;background:var(--white)}
  .slide--closing{top:2705px;background:linear-gradient(165deg,#7a10d4 0%,#5a34ea 55%,#3d66f2 100%)}

  .brand{position:absolute;display:flex;align-items:center;gap:10px;font-weight:500;font-size:22px;line-height:1.05;color:var(--white)}
  .brand__mark{width:14px;height:14px;background:currentColor;flex:none}
  .brand--dark{color:var(--heading-blue)}

  .title{position:absolute;font-weight:500;letter-spacing:.5px}
  .title--cover{left:38px;top:268px;font-size:42px;line-height:58px;color:var(--white)}
  .title--panel{left:38px;top:108px;font-size:42px;line-height:54px;background:linear-gradient(90deg,var(--heading-blue),var(--heading-violet));-webkit-background-clip:text;background-clip:text;color:transparent}

  .lead{position:absolute;left:38px;width:400px;font-size:12px;line-height:17px;color:var(--ink)}
  .subhead{position:absolute;left:38px;font-size:14.5px;font-weight:500;color:var(--ink)}
  .checklist{position:absolute;left:38px;width:400px;list-style:none;font-size:10.5px;line-height:14px}
  .checklist li{position:relative;padding-left:15px;margin-bottom:12px}
  .checklist li::before{content:"";position:absolute;left:0;top:2px;width:0;height:0;border-left:7px solid var(--ink);border-top:4px solid transparent;border-bottom:4px solid transparent}

  .footer{position:absolute;left:38px;top:594px;font-size:11.5px;font-weight:500;color:var(--ink);display:flex;gap:16px}
  .footer--light{color:var(--white)}

  .visual{position:absolute}
  .visual--frame{left:486px;top:0;width:616px;height:620px}
  .visual--cover{background:linear-gradient(135deg,#2a9cf0 0%,#6d4ee0 45%,#8a3fc9 100%)}
  .visual--light{background:linear-gradient(135deg,#1e8fe8 0%,#ffffff 30%,#ffffff 70%,#2b5ed6 100%)}
  .visual--photo{left:552px;top:122px;width:485px;height:375px;box-shadow:0 0 6px rgba(0,0,0,.25)}
  .visual--helix{background:linear-gradient(135deg,#cfeefb 0%,#7fcdf0 45%,#9e7ad8 70%,#cdeaf8 100%)}
  .visual--capsules{background:radial-gradient(circle at 50% 48%,#3b6fb8 0%,var(--navy) 35%,var(--navy) 100%)}
  .visual--closing-frame{left:0;top:0;width:616px;height:620px;background:linear-gradient(135deg,#2d7ff0 0%,#7a2fc8 40%,#2a6de8 100%)}
  .visual--lab{left:66px;top:123px;width:483px;height:375px;background:linear-gradient(135deg,#dbe9f6 0%,#8fb5dc 45%,#e9f2fa 100%)}

  .section-label{position:absolute;left:90px;top:56px;font-size:21px;font-weight:500;color:var(--white);letter-spacing:.3px}
  .column{position:absolute;top:145px;width:410px;color:var(--white)}
  .column--left{left:90px}
  .column--right{left:606px}
  .column__title{font-size:42px;font-weight:500;line-height:53px;margin-bottom:20px}
  .column__text{font-size:11.8px;line-height:20.8px;margin-bottom:20px}

  .gauges{position:absolute;left:38px;top:400px;display:flex;gap:38px}
  .gauge{width:102px;height:102px}
  .gauge text{font-family:"Montserrat",sans-serif;font-size:21px;font-weight:600}

  .closing{position:absolute;left:650px;width:420px;color:var(--white)}
  .closing__title{top:165px;font-size:43px;font-weight:500;line-height:55px}
  .closing__text{top:282px;font-size:12px;line-height:17px}
  .contact{position:absolute;display:flex;align-items:center;gap:12px;color:var(--white);font-size:12.5px;line-height:21px}
  .contact__icon{width:36px;height:36px;flex:none}
</style>
</head>
<body>

<section class="slide slide--cover">
  <div class="brand" style="left:38px;top:45px"><span class="brand__mark"></span>Corvane<br>Therapeutics</div>
  <h1 class="title title--cover">Neque porro<br>quisquam est qui<br>dolorem ipsum</h1>
  <div class="footer footer--light"><span>www.CorvaneTherapeutics.com</span><span>|</span><span>+0123 456 7890</span></div>
  <div class="visual visual--frame visual--cover" role="img" aria-label="Researcher at a microscope in a purple tint, framed by bold diagonal stripes"></div>
</section>

<section class="slide slide--genetics">
  <div class="brand brand--dark" style="left:38px;top:26px"><span class="brand__mark"></span>Corvane<br>Therapeutics</div>
  <h2 class="title title--panel">Neque porro<br>quisquam est qui</h2>
  <p class="lead" style="top:222px">Sed ut perspiciatis unde omnis iste natus error sit voluptatem accusantium doloremque laudantium, totam rem aperiam, eaque ipsa quae ab illo inventore veritatis et quasi architecto beatae vitae dicta sunt explicabo.</p>
  <p class="subhead" style="top:305px">Nemo enim ipsam voluptatem quia voluptas</p>
  <ul class="checklist" style="top:340px">
    <li>Sed ut perspiciatis unde omnis iste natus error sit voluptatem</li>
    <li>Doloremque laudantium, totam rem aperiam, eaque ipsa quae ab illo inventore veritatis et quasi architecto</li>
    <li>Beatae vitae dicta sunt explicabo.</li>
    <li>Sed ut perspiciatis unde omnis iste natus error sit voluptatem</li>
    <li>Doloremque laudantium, totam rem aperiam, eaque ipsa quae ab illo inventore veritatis et quasi architecto</li>
    <li>Beatae vitae dicta sunt explicabo.</li>
  </ul>
  <div class="footer"><span>www.CorvaneTherapeutics.com</span><span>|</span><span>+0123 456 7890</span></div>
  <div class="visual visual--frame visual--light" role="img" aria-label="Diagonal stripe frame decoration in blue and purple"></div>
  <div class="visual visual--photo visual--helix" role="img" aria-label="Rendered chromosome on a pale blue cellular background"></div>
</section>

<section class="slide slide--columns">
  <p class="section-label">QUISQUAM EST QUI DOLOREM IPSUM</p>
  <div class="brand" style="left:918px;top:42px"><span class="brand__mark"></span>Corvane<br>Therapeutics</div>
  <article class="column column--left">
    <h3 class="column__title">Quisquam est qui<br>dolorem ipsum</h3>
    <p class="column__text">Sed ut perspiciatis unde omnis iste natus error sit voluptatem accusantium doloremque laudantium, totam rem aperiam, eaque ipsa quae ab illo inventore veritatis et quasi architecto beatae vitae dicta sunt explicabo. Nemo enim ipsam voluptatem quia voluptas sit aspernatur aut odit aut fugit, sed quia consequuntur magni dolores eos qui ratione voluptatem sequi nesciunt. Neque porro quisquam est, qui dolorem ipsum quia dolor sit amet, consectetur, adipisci velit, sed quia non numquam eius modi tempora incidunt ut labore et dolore..</p>
    <p class="column__text">Ut enim ad minima veniam, quis nostrum exercitationem ullam corporis suscipit laboriosam, nisi ut aliquid ex ea commodi consequatur? Quis autem vel eum iure reprehenderit qui in ea</p>
  </article>
  <article class="column column--right">
    <h3 class="column__title">Quisquam est qui<br>dolorem ipsum</h3>
    <p class="column__text">Sed ut perspiciatis unde omnis iste natus error sit voluptatem accusantium doloremque laudantium, totam rem aperiam, eaque ipsa quae ab illo inventore veritatis et quasi architecto beatae vitae dicta sunt explicabo. Nemo enim ipsam voluptatem quia voluptas sit aspernatur aut odit aut fugit, sed quia consequuntur magni dolores eos qui ratione voluptatem sequi nesciunt. Neque porro quisquam est, qui dolorem ipsum quia dolor sit amet, consectetur, adipisci velit, sed quia non numquam eius modi tempora incidunt ut labore et dolore..</p>
    <p class="column__text">Ut enim ad minima veniam, quis nostrum exercitationem ullam corporis suscipit laboriosam, nisi ut aliquid ex ea commodi consequatur? Quis autem vel eum iure reprehenderit qui in ea</p>
  </article>
  <div class="footer footer--light"><span>www.CorvaneTherapeutics.com</span><span>|</span><span>+0123 456 7890</span></div>
</section>

<section class="slide slide--metrics">
  <div class="brand brand--dark" style="left:38px;top:26px"><span class="brand__mark"></span>Corvane<br>Therapeutics</div>
  <h2 class="title title--panel">Neque porro<br>quisquam est qui</h2>
  <p class="lead" style="top:222px">Sed ut perspiciatis unde omnis iste natus error sit voluptatem accusantium doloremque laudantium, totam rem aperiam</p>
  <p class="subhead" style="top:272px">Nemo enim ipsam voluptatem quia voluptas</p>
  <ul class="checklist" style="top:307px">
    <li>Sed ut perspiciatis unde omnis iste natus error sit voluptatem</li>
    <li>Doloremque laudantium, totam rem aperiam, eaque ipsa quae ab illo inventore veritatis et quasi architecto</li>
  </ul>
  <div class="gauges">
    <svg class="gauge" viewBox="0 0 102 102"><circle cx="51" cy="51" r="45" fill="none" stroke="var(--indigo)" stroke-width="7" stroke-dasharray="184 283" transform="rotate(90 51 51)"/><text x="51" y="58" text-anchor="middle" fill="var(--indigo)">65%</text></svg>
    <svg class="gauge" viewBox="0 0 102 102"><circle cx="51" cy="51" r="45" fill="none" stroke="var(--cyan)" stroke-width="7" stroke-dasharray="240 283" transform="rotate(120 51 51)"/><text x="51" y="58" text-anchor="middle" fill="var(--cyan)">85%</text></svg>
    <svg class="gauge" viewBox="0 0 102 102"><circle cx="51" cy="51" r="45" fill="none" stroke="var(--plum)" stroke-width="7" stroke-dasharray="269 283" transform="rotate(110 51 51)"/><text x="51" y="58" text-anchor="middle" fill="var(--plum)">95%</text></svg>
  </div>
  <div class="footer"><span>www.CorvaneTherapeutics.com</span><span>|</span><span>+0123 456 7890</span></div>
  <div class="visual visual--frame visual--light" role="img" aria-label="Diagonal stripe frame decoration in blue and purple"></div>
  <div class="visual visual--photo visual--capsules" role="img" aria-label="Scattered colourful pills and capsules on a dark navy background"></div>
</section>

<section class="slide slide--closing">
  <div class="visual visual--closing-frame" role="img" aria-label="Diagonal stripe frame decoration in blue and purple"></div>
  <div class="visual visual--lab" role="img" aria-label="Gloved hand with a pipette over a petri dish and sample tray in a lab"></div>
  <div class="brand" style="left:914px;top:30px"><span class="brand__mark"></span>Corvane<br>Therapeutics</div>
  <h2 class="closing closing__title">Thank You!<br>quisquam est qui</h2>
  <p class="closing closing__text">Sed ut perspiciatis unde omnis iste natus error sit voluptatem accusantium doloremque laudantium, totam rem aperiam</p>
  <div class="contact" style="left:647px;top:339px">
    <svg class="contact__icon" viewBox="0 0 36 36"><circle cx="18" cy="18" r="16.5" fill="none" stroke="#29b8e8" stroke-width="2"/><path d="M13 11.5l3 0 1.2 3.5-2 1.4c.9 2 2.3 3.4 4.3 4.3l1.4-2 3.5 1.2 0 3c0 .8-.7 1.5-1.5 1.5C16.5 24.4 11.6 19.5 11.5 13c0-.8.7-1.5 1.5-1.5z" fill="#fff"/></svg>
    <div>Phone:<br>+0123 456 7890</div>
  </div>
  <div class="contact" style="left:848px;top:339px">
    <svg class="contact__icon" viewBox="0 0 36 36"><circle cx="18" cy="18" r="16.5" fill="none" stroke="#29b8e8" stroke-width="2"/><rect x="11" y="13" width="14" height="10" rx="1" fill="#fff"/><path d="M11 13.5l7 5 7-5" fill="none" stroke="#5a34ea" stroke-width="1.5"/></svg>
    <div>Email:<br>info@company.com</div>
  </div>
  <div class="contact" style="left:647px;top:422px">
    <svg class="contact__icon" viewBox="0 0 36 36"><circle cx="18" cy="18" r="16.5" fill="none" stroke="#29b8e8" stroke-width="2"/><path d="M18 10c-3 0-5.3 2.3-5.3 5.2 0 3.9 5.3 10 5.3 10s5.3-6.1 5.3-10C23.3 12.3 21 10 18 10z" fill="#fff"/><circle cx="18" cy="15.3" r="2" fill="#5a34ea"/></svg>
    <div>1870 Larkspur Ridge Rd<br>#210 Easton, Or 97450</div>
  </div>
</section>

</body>
</html>
```